Hardcore nerd needs to stand out in a sea of dull Defence business cards

Wombarra Devices is a new Australian consulting engineering company that turns research and theory into practical systems. No evangelistic fluff, just mathematics and physics into electronic and optical circuits for consumer products, scientific research or Defence applications.

We already have a recognised logo (provided) which is often dark blue/black on a light background but we're open to other combinations. (Us engineers tend to have limited aesthetic imagination :)

Some of our recent products have included:
* Instrumentation for electrical testing,
* Radar jammers,
* GPS antenna design,
* Satellite tracking systems,
* High power lasers

We're open to both single and double-sided designs - happy to be convinced either way.

P.S. Another group is working on the web page, so - alas - our web site is currently of no use for images/ideas...

Target Market(s)

Engineering managers,
Scientists

Contact Information for Business Card

Dr Colin Harte
R&D Engineer

colin@wombarradevices.com.au
0427 563 710

PO Box XXX (to be confirmed)
Kelsby ACT 2917
Australia

Font styles to use
Serif
Sans Serif

Colors

Designer to choose colors to be used in the design.

Requirements
Must have
• My contact details!
• I've had many (great) "bold and plain" designs submitted already, so feel free to be artistically creative :)
• Happy to take advice re fonts/colours/printability etc.
Nice to have
• I'm not sure if "lists" are more at home on a CV than a business card, but representative services include:
• Applied electromagnetics
• RF and high speed electronics
• Signal and image processing
• Electro-optical and laser systems
• Concept-to-prototype design services
• If you're considering double sided cards, then often measuring/alignment grids/rulers feature on the back of similar cards.
• e.g. https://www.veltranoptics.example/newgrouppage9.cfm?objectgroup_id=4183
• https://www.veltranoptics.example/newgrouppage9.cfm?objectgroup_ID=4185
• ..or even a "Smith chart" (google will return lots)
• Generic images to represent a capability might work - googling images associated with keyword for each of these areas might help:
• - "passive radar", "phased array", "fdtd", "vircator"
• RF and high speed electronic design
• - "smith chart", "microstrip circuits", "dimensioned drawing", "electronic schematic"
• - "dft", "iir filter"
• - "optical cavity". "laser energy level diagram"
• Background/watermarked images outlines/wireframes/schematics would probably look OK.
Should not have
• If a list of projects/services is provided, it is important not to make the client feel that this is "all" the company can do. Engineering design is a creative discipline (like graphics :)
• Please, no stock "military" snaps like planes, missiles, etc!

```html
<!DOCTYPE html>
<html lang="en">
<head>
<meta charset="utf-8">
<title>Wombarra Devices – Business Card</title>
<link rel="stylesheet" href="https://fonts.googleapis.com/css2?family=Lato:wght@400;700;900&display=swap">
<style>
  :root {
    --stage: #3b3735;
    --card-red: #e61f2c;
    --card-dark: #2a2829;
    --accent-blue: #25397f;
    --logo-ink: #1c1f3a;
    --text-light: #ffffff;
    --text-soft: #e9e6e6;
  }
  * { box-sizing: border-box; margin: 0; padding: 0; }
  html, body {
    width: 1200px;
    height: 768px;
    overflow: hidden;
  }
  body {
    background: var(--stage);
    font-family: "Lato", "Helvetica Neue", Arial, sans-serif;
    position: relative;
  }
  .card {
    position: absolute;
    top: 239px;
    width: 520px;
    height: 290px;
    overflow: hidden;
    box-shadow: 0 14px 30px rgba(0,0,0,.45);
  }
  .card--front { left: 50px; background: var(--card-red); }
  .card--back  { left: 630px; display: flex; }

  /* logo wordmark */
  .wordmark {
    display: flex;
    align-items: center;
    gap: 10px;
    color: var(--logo-ink);
    font-weight: 900;
    text-transform: uppercase;
    line-height: 1;
  }
  .wordmark__dot {
    flex: none;
    border-radius: 50%;
    background: var(--logo-ink);
  }

  /* front */
  .front__logo {
    position: absolute;
    top: 62px;
    left: 0;
    width: 100%;
    justify-content: center;
    font-size: 21px;
    letter-spacing: 1px;
  }
  .front__logo .wordmark__dot { width: 26px; height: 26px; }
  .capabilities {
    position: absolute;
    top: 128px;
    left: 0;
    width: 100%;
    list-style: none;
    text-align: center;
    color: var(--text-light);
    font-weight: 700;
    font-size: 16px;
    line-height: 21px;
  }

  /* back */
  .back__info {
    width: 312px;
    height: 100%;
    background: var(--card-dark);
    color: var(--text-soft);
    padding: 42px 0 0 0;
    position: relative;
  }
  .info-block {
    position: relative;
    padding-left: 34px;
  }
  .info-block::before {
    content: "";
    position: absolute;
    left: 16px;
    top: 0;
    width: 8px;
    height: 100%;
    background: var(--accent-blue);
  }
  .person__name {
    color: var(--card-red);
    font-weight: 700;
    font-size: 19px;
    line-height: 22px;
  }
  .person__title {
    font-size: 13px;
    line-height: 17px;
    color: var(--text-light);
  }
  .address {
    margin-top: 38px;
    font-size: 14px;
    line-height: 19px;
    color: var(--text-light);
  }
  .contact {
    list-style: none;
    margin-top: 10px;
    padding-left: 34px;
    font-size: 14px;
    line-height: 22px;
    color: var(--text-light);
  }
  .contact__item { display: flex; align-items: center; gap: 6px; }
  .contact__icon { width: 13px; height: 13px; flex: none; }

  .back__brand {
    flex: 1;
    background: var(--card-red);
    display: flex;
    align-items: center;
    justify-content: center;
  }
  .back__brand .wordmark {
    flex-direction: column;
    gap: 8px;
    font-size: 22px;
    text-align: center;
    letter-spacing: 1px;
  }
  .back__brand .wordmark__dot { width: 40px; height: 40px; }
</style>
</head>
<body>

  <section class="card card--front" aria-label="Card front">
    <div class="wordmark front__logo">
      <span class="wordmark__dot"></span>
      <span>Wombarra Devices</span>
    </div>
    <ul class="capabilities">
      <li>Radar jammers</li>
      <li>High power lasers</li>
      <li>GPS antenna design</li>
      <li>Satellite tracking systems</li>
      <li>Instrumentation for electrical testing</li>
    </ul>
  </section>

  <section class="card card--back" aria-label="Card back">
    <div class="back__info">
      <div class="info-block person">
        <p class="person__name">Dr Colin Harte</p>
        <p class="person__title">R&amp;D Engineer</p>
      </div>
      <div class="info-block address">
        <p>PO Box XXX</p>
        <p>Kelsby ACT 2917, Australia</p>
      </div>
      <ul class="contact">
        <li class="contact__item">
          <svg class="contact__icon" viewBox="0 0 14 14" aria-hidden="true">
            <circle cx="7" cy="7" r="7" fill="#e61f2c"/>
            <path d="M4.3 3.6l1.4-.3.8 1.8-.9.7a5 5 0 0 0 2.5 2.5l.7-.9 1.8.8-.3 1.4c-3.4.2-6.2-2.6-6-6z" fill="#2a2829"/>
          </svg>
          <span>0427 563 710</span>
        </li>
        <li class="contact__item">
          <svg class="contact__icon" viewBox="0 0 14 14" aria-hidden="true">
            <circle cx="7" cy="7" r="7" fill="#e61f2c"/>
            <rect x="3.5" y="4.5" width="7" height="5" fill="none" stroke="#2a2829" stroke-width="1"/>
            <path d="M3.5 4.5L7 7.3l3.5-2.8" fill="none" stroke="#2a2829" stroke-width="1"/>
          </svg>
          <span>colin@wombarradevices.com.au</span>
        </li>
      </ul>
    </div>
    <div class="back__brand">
      <div class="wordmark">
        <span class="wordmark__dot"></span>
        <span>Wombarra<br>Devices</span>
      </div>
    </div>
  </section>

</body>
</html>
```